Hvac and insulation company needs good looking business card design

We are hvac and insulation company and looking for a new business cards that look to today standards designs

Target Market(s)

homeowners

Industry/Entity Type

Hvac

Contact Information for Business Card

Name: Walter Brinoku
Home comfort consultant
address: 4827 Dunmore St #215 Oakland, CA 94619
office: 888-316-2790
cell: 510-742-3185
Lic.# 584261
Email: walter@corvane-hvac.com
Web: corvane-hvac.com

Requirements
Must have
• clean and sleek look
Nice to have
• simple with a clean look
Should not have
• to busy business card

```html
<!DOCTYPE html>
<html lang="en">
<head>
<meta charset="utf-8">
<title>Corvane Business Card</title>
<link href="https://fonts.googleapis.com/css2?family=Lato:wght@400;700&display=swap" rel="stylesheet">
<style>
  :root {
    --brand-orange: #f5841f;
    --paper: #ffffff;
    --ink-grey: #6d6e71;
    --band-grey: #8a8a8a;
    --rule-grey: #9a9a9a;
    --backdrop: #e9ecef;
  }
  * { margin: 0; padding: 0; box-sizing: border-box; }
  html, body {
    width: 1200px; height: 1000px; overflow: hidden;
    background: var(--backdrop);
    font-family: "Lato", sans-serif;
  }
  .canvas { position: relative; width: 1200px; height: 1000px; }
  .card {
    position: absolute; left: 250px; width: 700px; height: 400px;
    box-shadow: 0 10px 28px rgba(0,0,0,0.18);
    overflow: hidden;
  }
  .card-front { top: 60px; background: var(--brand-orange); color: var(--paper); }
  .card-back { top: 540px; background: var(--paper); color: var(--ink-grey); }

  .brand { position: absolute; display: flex; align-items: center; gap: 14px; font-weight: 700; line-height: 1; }
  .brand-mark { display: block; }
  .card-front .brand { left: 50%; top: 50%; transform: translate(-50%, -58%); font-size: 64px; }
  .card-front .brand-mark { width: 40px; height: 40px; background: var(--paper); }
  .card-back .brand { right: 30px; top: 46px; font-size: 46px; color: var(--brand-orange); }
  .card-back .brand-mark { width: 30px; height: 30px; background: var(--brand-orange); }

  .website { position: absolute; right: 62px; bottom: 30px; font-size: 20px; }

  .person { position: absolute; left: 36px; top: 112px; }
  .person-name { font-size: 39px; font-weight: 400; line-height: 1.1; }
  .person-title { font-size: 21px; margin-top: 2px; }

  .rule { position: absolute; left: 33px; right: 0; top: 196px; height: 2px; background: var(--rule-grey); }
  .address-band {
    position: absolute; left: 213px; right: 0; top: 196px; height: 34px;
    background: var(--band-grey);
    clip-path: polygon(0 0, 100% 0, 100% 100%, 22px 100%);
    color: var(--paper); font-size: 18.5px;
    display: flex; align-items: center; justify-content: flex-end; padding-right: 30px;
  }

  .contacts { position: absolute; left: 44px; top: 248px; list-style: none; }
  .contacts li { display: flex; align-items: center; height: 36px; font-size: 24px; }
  .contacts svg { width: 20px; height: 20px; margin-right: 18px; fill: var(--ink-grey); }
  .license { position: absolute; right: 30px; top: 348px; font-size: 17px; }
</style>
</head>
<body>
<div class="canvas">

  <section class="card card-front">
    <div class="brand"><span class="brand-mark"></span><span class="brand-name">corvane</span></div>
    <div class="website">www.corvane-hvac.com</div>
  </section>

  <section class="card card-back">
    <div class="brand"><span class="brand-mark"></span><span class="brand-name">corvane</span></div>

    <div class="person">
      <h1 class="person-name">Walter Brinoku</h1>
      <p class="person-title">Home comfort consultant</p>
    </div>

    <div class="rule"></div>
    <div class="address-band">4827 Dunmore St #215 Oakland, CA 94619</div>

    <ul class="contacts">
      <li>
        <svg viewBox="0 0 20 20" aria-hidden="true"><path d="M2 6c0-2 3-3 8-3s8 1 8 3v2h-4V6.5H6V8H2z"/><path d="M5 9h10l2 8H3z"/><circle cx="10" cy="13" r="2" fill="#fff"/></svg>
        888-316-2790
      </li>
      <li>
        <svg viewBox="0 0 20 20" aria-hidden="true"><path d="M5 2l3 4-2 2c1 2.5 3.5 5 6 6l2-2 4 3-2 3C9 18 2 11 2 4z"/></svg>
        510-742-3185
      </li>
      <li>
        <svg viewBox="0 0 20 20" aria-hidden="true"><path d="M2 5h16v11H2z"/><path d="M2 5l8 6 8-6" fill="none" stroke="#fff" stroke-width="1.5"/></svg>
        walter@corvane-hvac.com
      </li>
    </ul>

    <div class="license">Lic.# 584261</div>
  </section>

</div>
</body>
</html>
```